Tidy-Nook- Home Organization and Staging Company needs Logo and Business Cards

I would like eclectic, but classy business card design for my Home Organization/Home Staging business. I would really like to incorporate a little princess crown “cocked“ to the left side of hanger to I am also going to order some post card flyers very soon. As quickly as I can figure out what exact information I want on it.

Target Market(s)

Realtors, Homeowners, Interior Designers

Contact Information for Business Card

Mara Lentz
Owner/Consultant
Phone -(919) 555-0173
Email- Maralz207@nestmail.example
Website- www.Tidy-Nestle.example

Font styles to use
Script

Colors
e34197
e667a6
eea4c8

Requirements
Nice to have
• Please try add a little piano chair under the house. See updates photos below for example.

```html
<!DOCTYPE html>
<html lang="en">
<head>
<meta charset="utf-8">
<title>Tidy-Nook Business Cards</title>
<link rel="stylesheet" href="https://fonts.googleapis.com/css2?family=Quicksand:wght@300;400;500&family=Open+Sans:wght@400;600&display=swap">
<style>
  :root {
    --stage: #5a2840;
    --card-front: #f3dde8;
    --card-back: #d46d99;
    --brand-pink: #d9669d;
    --brand-soft: #eea4c8;
    --ink: #3a3a3a;
    --white: #fdf4f8;
    --ornament-a: rgba(240, 160, 196, 0.55);
    --ornament-b: rgba(212, 109, 153, 0);
  }
  * { box-sizing: border-box; margin: 0; padding: 0; }
  html, body { width: 1200px; height: 900px; overflow: hidden; }
  body {
    background: var(--stage);
    font-family: "Quicksand", "Century Gothic", sans-serif;
    position: relative;
  }
  .card {
    position: absolute;
    width: 525px;
    height: 300px;
    border-radius: 3px;
    box-shadow: 0 14px 30px rgba(30, 8, 20, 0.45);
    overflow: hidden;
  }

  /* Front card */
  .card--front {
    left: 70px;
    top: 470px;
    background: var(--card-front);
  }
  .front__brand {
    position: absolute;
    left: 0; right: 0; top: 52px;
    display: flex;
    align-items: center;
    justify-content: center;
    gap: 12px;
  }
  .brand-dot {
    width: 16px; height: 16px;
    border-radius: 50%;
    background: var(--brand-pink);
  }
  .brand-name {
    font-size: 44px;
    font-weight: 400;
    color: var(--brand-pink);
    letter-spacing: 0.5px;
    white-space: nowrap;
  }
  .front__person {
    position: absolute;
    left: 0; right: 0; top: 132px;
    text-align: center;
  }
  .person-name {
    font-size: 22px;
    font-weight: 300;
    letter-spacing: 2px;
    color: var(--ink);
  }
  .person-title {
    font-size: 12px;
    font-weight: 500;
    letter-spacing: 2px;
    color: var(--brand-pink);
    margin-top: 2px;
  }
  .front__contact {
    position: absolute;
    left: 30px; right: 30px; bottom: 34px;
    display: flex;
    justify-content: space-between;
    list-style: none;
    font-family: "Open Sans", Arial, sans-serif;
    font-size: 12.5px;
    color: var(--ink);
  }
  .contact-item { display: flex; align-items: center; gap: 7px; white-space: nowrap; }
  .contact-item svg { width: 13px; height: 13px; fill: var(--brand-pink); flex: none; }

  /* Back card */
  .card--back {
    left: 605px;
    top: 130px;
    background: var(--card-back);
  }
  .back__ornament {
    position: absolute;
    left: 150px; top: 10px;
    width: 300px; height: 280px;
    border-radius: 50%;
    background: radial-gradient(ellipse at center, var(--ornament-a), var(--ornament-b) 70%);
  }
  .back__content {
    position: absolute;
    left: 0; right: 0; top: 78px;
    text-align: center;
    color: var(--white);
  }
  .back__brand {
    display: flex;
    align-items: center;
    justify-content: center;
    gap: 12px;
  }
  .back__brand .brand-dot { background: var(--white); }
  .back__brand .brand-name { color: var(--white); }
  .tagline {
    margin-top: 14px;
    font-size: 19px;
    font-weight: 300;
    letter-spacing: 1px;
  }
  .tagline .sep { font-size: 12px; vertical-align: middle; margin: 0 8px; }
  .values {
    margin-top: 10px;
    font-family: "Open Sans", Arial, sans-serif;
    font-size: 9px;
    letter-spacing: 1.2px;
  }
</style>
</head>
<body>

  <section class="card card--back" aria-label="Business card back">
    <div class="back__ornament" role="img" aria-label="Faint swirl ornament behind the brand name"></div>
    <div class="back__content">
      <div class="back__brand">
        <span class="brand-dot"></span>
        <span class="brand-name">Tidy-Nook</span>
      </div>
      <p class="tagline">Sorted<span class="sep">●</span>Organized<span class="sep">●</span>Staged</p>
      <p class="values">CLIENT CONSCIOS | CLEAN INSPIRATION | CLASSY STYLE</p>
    </div>
  </section>

  <section class="card card--front" aria-label="Business card front">
    <div class="front__brand">
      <span class="brand-dot"></span>
      <span class="brand-name">Tidy-Nook</span>
    </div>
    <div class="front__person">
      <p class="person-name">YOUR NAME</p>
      <p class="person-title">JOB TITLE</p>
    </div>
    <ul class="front__contact">
      <li class="contact-item">
        <svg viewBox="0 0 16 16" aria-hidden="true"><path d="M3.6 1.2l2.3 2.6-1.3 1.9c.9 2 2.5 3.6 4.6 4.6l1.9-1.3 2.6 2.3-1.4 2.4C6.8 13.5 2.5 9.2 1.2 3.7z"/></svg>
        <span>000 000 0000</span>
      </li>
      <li class="contact-item">
        <svg viewBox="0 0 16 16" aria-hidden="true"><rect x="1" y="3" width="14" height="10"/><path d="M1.8 3.6L8 8.6l6.2-5" fill="none" stroke="#f3dde8" stroke-width="1.2"/></svg>
        <span>youremail@xyz.com</span>
      </li>
      <li class="contact-item">
        <svg viewBox="0 0 16 16" aria-hidden="true"><circle cx="8" cy="8" r="7"/><path d="M1 8h14M8 1c-3 3.5-3 10.5 0 14M8 1c3 3.5 3 10.5 0 14" fill="none" stroke="#f3dde8" stroke-width="1"/></svg>
        <span>www.yourwebsite.com</span>
      </li>
    </ul>
  </section>

</body>
</html>
```